business card deign

Logo needs the following on it.
1. attached logo
2. Tagline - "If it keeps a drink cold or the party going...we do it!"
3. Name- Dalton Pikes, Founder and CPO
4. Address - 412 E. Carver Avenue, Ste 2207, Tampa, FL. 33917
5. Phone - 555.318.4726

```html
<!DOCTYPE html>
<html lang="en">
<head>
<meta charset="utf-8">
<title>Koolmate Business Card</title>
<link rel="stylesheet" href="https://fonts.googleapis.com/css2?family=Roboto:wght@400;500;700&display=swap">
<style>
  :root {
    --backdrop: #dcdcdc;
    --card: #161616;
    --ink: #ffffff;
    --ink-soft: #e6e6e6;
    --rule: #bdbdbd;
    --ghost: #242424;
  }
  * { margin: 0; padding: 0; box-sizing: border-box; }
  html, body { width: 1200px; height: 711px; overflow: hidden; }
  body {
    background: radial-gradient(ellipse at 60% 40%, #f2f2f2 0%, var(--backdrop) 70%);
    font-family: "Roboto", Arial, sans-serif;
    color: var(--ink);
    position: relative;
  }
  .card {
    position: absolute;
    width: 540px;
    height: 309px;
    background: var(--card);
    border-radius: 28px;
    box-shadow: 0 14px 28px rgba(0,0,0,.35);
    overflow: hidden;
  }
  .card--front { left: 70px; top: 60px; }
  .card--back { left: 600px; top: 350px; }

  .brand {
    display: flex;
    align-items: center;
    gap: 14px;
  }
  .brand__dot {
    width: 18px; height: 18px; border-radius: 50%;
    background: var(--ink);
  }
  .brand__name {
    font-weight: 700;
    letter-spacing: .32em;
    color: var(--ink);
  }
  .card--front .brand {
    position: absolute; left: 0; right: 0; top: 128px;
    justify-content: center;
  }
  .card--front .brand__name { font-size: 42px; }

  .card--back .brand { position: absolute; left: 38px; top: 78px; }
  .card--back .brand__dot { width: 14px; height: 14px; }
  .card--back .brand__name { font-size: 28px; }

  .ghost-mark {
    position: absolute; right: 40px; top: 20px;
    width: 150px; height: 150px; border-radius: 50%;
    background: var(--ghost);
  }
  .id-bar {
    position: absolute; right: 0; top: 34px;
    width: 16px; height: 58px; background: var(--ink);
  }
  .person {
    position: absolute; right: 34px; top: 40px; text-align: right;
  }
  .person__name { font-size: 26px; font-weight: 700; }
  .person__role { font-size: 14px; color: var(--ink-soft); margin-top: 4px; }
  .rule-short {
    position: absolute; right: 34px; top: 100px;
    width: 150px; height: 1px; background: var(--rule);
  }
  .rule-long {
    position: absolute; left: 38px; right: 200px; top: 170px;
    height: 1px; background: var(--rule);
  }
  .contact {
    position: absolute; left: 38px; top: 200px;
    list-style: none; font-size: 14px; line-height: 1.45;
  }
  .contact li { display: flex; align-items: flex-start; gap: 10px; }
  .contact svg { width: 13px; height: 13px; margin-top: 3px; flex: none; }
  .tagline {
    position: absolute; right: 34px; top: 140px;
    width: 180px; text-align: right;
    font-size: 13px; line-height: 1.45; color: var(--ink-soft);
  }
</style>
</head>
<body>
  <section class="card card--front" aria-label="Card front">
    <div class="brand">
      <span class="brand__dot"></span>
      <span class="brand__name">KOOLMATE</span>
    </div>
  </section>

  <section class="card card--back" aria-label="Card back">
    <div class="ghost-mark" aria-hidden="true"></div>
    <div class="brand">
      <span class="brand__dot"></span>
      <span class="brand__name">KOOLMATE</span>
    </div>
    <div class="id-bar"></div>
    <div class="person">
      <p class="person__name">Dalton Pikes</p>
      <p class="person__role">Founder and CPO</p>
    </div>
    <div class="rule-short"></div>
    <p class="tagline">If it keeps a drink cold or the party going...we do it!</p>
    <div class="rule-long"></div>
    <ul class="contact">
      <li>
        <svg viewBox="0 0 24 24" fill="none" stroke="#fff" stroke-width="2.2"><path d="M5 3h4l2 5-2.5 1.5a11 11 0 0 0 6 6L16 13l5 2v4a2 2 0 0 1-2 2A17 17 0 0 1 3 5a2 2 0 0 1 2-2z"/></svg>
        <span>555.318.4726</span>
      </li>
      <li>
        <svg viewBox="0 0 24 24" fill="none" stroke="#fff" stroke-width="2.2"><path d="M12 22s7-7 7-12a7 7 0 0 0-14 0c0 5 7 12 7 12z"/><circle cx="12" cy="10" r="2.5"/></svg>
        <span>412 E. Carver Avenue,<br>Ste 2207, Tampa, FL. 33917</span>
      </li>
    </ul>
  </section>
</body>
</html>
```